Logistics Website Design

See website https://tqfreightglobal.com for theme and color details. Need the site to be re-done and reflect some of the designs shown in this list here: https://pixelvane.com/tags/logistics-company-website

Target Market(s)

Logistics & Transportation

Industry/Entity Type

Logistics and Supply Chain

Coding

Number of Pages Required

5+ page

Requirements
Must have
• Colors must match theme of logo. Looking for a sleek, interactive design.

```html
<!DOCTYPE html>
<html lang="en">
<head>
<meta charset="utf-8">
<title>TQFREIGHT — Driving Global Commerce</title>
<link href="https://fonts.googleapis.com/css2?family=Inter:wght@400;500;600;700;800;900&display=swap" rel="stylesheet">
<style>
  :root{
    --ink:#121212;
    --ink-2:#1c1211;
    --card:#1d1413;
    --card-line:#3a2b27;
    --icon-bg:#34211b;
    --accent:#ee9460;
    --white:#ffffff;
    --cream:#fbf0e8;
    --dark-text:#1e1614;
    --body-dark:#3a302c;
    --muted:#c9bdb8;
    --faint:#a89c97;
  }
  *{margin:0;padding:0;box-sizing:border-box}
  html,body{width:703px;height:1200px;overflow:hidden}
  body{font-family:"Inter",sans-serif;background:var(--ink);color:var(--white);position:relative}

  /* hero */
  .hero{position:absolute;left:0;top:0;width:703px;height:387px;background:var(--ink);overflow:hidden}
  .hero-photo{position:absolute;inset:0;
    clip-path:polygon(340px 0,703px 0,703px 387px,282px 387px);
    background:
      radial-gradient(ellipse 140px 90px at 630px 175px,rgba(240,160,80,.75),rgba(0,0,0,0) 70%),
      radial-gradient(ellipse 260px 120px at 560px 80px,rgba(170,110,55,.8),rgba(0,0,0,0) 75%),
      linear-gradient(180deg,#3a2a1e 0%,#5a3f27 22%,#3b3330 45%,#2a2624 70%,#2e2823 100%);}
  .site-nav{position:absolute;left:0;top:0;width:703px;height:37px;background:rgba(18,18,18,.85);border-bottom:1px solid #2a2a2a;z-index:2}
  .brand{position:absolute;left:72px;top:11px;font-weight:800;font-size:11.5px;letter-spacing:.8px;color:var(--accent)}
  .nav-links{position:absolute;right:73px;top:14px;display:flex;gap:14px;font-size:7px;font-weight:500;list-style:none}
  .hero-title{position:absolute;left:72px;top:104px;font-weight:900;font-size:37.5px;line-height:37px;letter-spacing:-1.3px}
  .hero-title .accent{color:var(--accent)}
  .hero-sub{position:absolute;left:72px;top:225px;font-size:9px;line-height:14.5px;width:180px}
  .btn{position:absolute;left:72px;top:272px;width:72px;height:20px;border-radius:3px;background:var(--accent);color:var(--ink);font-weight:600;font-size:7.6px;display:flex;align-items:center;justify-content:center}

  /* about */
  .about{position:absolute;left:0;top:387px;width:703px;height:182px;background:var(--cream);color:var(--dark-text)}
  .eyebrow{position:absolute;left:72px;top:46px;font-size:11.5px;font-weight:700;color:var(--accent)}
  .about-title{position:absolute;left:72px;top:71px;font-size:31px;line-height:32px;font-weight:800;letter-spacing:-.5px}
  .about-copy{position:absolute;left:324px;top:47px;width:310px;font-size:8.3px;line-height:14.7px;color:var(--body-dark)}
  .about-copy p+p{margin-top:14px}

  /* services */
  .services-title{position:absolute;left:0;width:703px;top:615px;text-align:center;font-size:23px;font-weight:800;letter-spacing:-.3px}
  .services-title span{color:var(--accent)}
  .card{position:absolute;width:272px;height:131px;background:var(--card);border:1px solid var(--card-line);border-radius:5px}
  .card-icon{position:absolute;left:19px;top:19px;width:32px;height:32px;border-radius:4px;background:var(--icon-bg);display:flex;align-items:center;justify-content:center}
  .card h3{position:absolute;left:19px;top:65px;font-size:11.5px;font-weight:700}
  .card p{position:absolute;left:19px;top:88px;width:230px;font-size:7.7px;line-height:12px;color:var(--muted)}

  /* footer */
  .site-footer{position:absolute;left:0;top:992px;width:703px;height:208px;background:var(--ink-2);border-top:1px solid #2a2220}
  .foot-brand{position:absolute;left:72px;top:36px;font-size:13.5px;font-weight:800;color:var(--accent)}
  .foot-about{position:absolute;left:72px;top:63px;width:150px;font-size:7.4px;line-height:12px;color:var(--muted)}
  .foot-col{position:absolute;top:39px}
  .foot-col h4{font-size:8.6px;font-weight:700;position:relative;padding-bottom:7px}
  .foot-col h4::after{content:"";position:absolute;left:0;bottom:0;width:14px;height:1px;background:var(--accent)}
  .foot-col ul{list-style:none;margin-top:10px;font-size:7.2px;font-weight:400;color:var(--faint)}
  .foot-col li{height:18.3px;display:flex;align-items:center;gap:3px}
  .foot-col.contact li{color:var(--muted)}
  .foot-rule{position:absolute;left:72px;top:160px;width:558px;height:1px;background:#2e2523}
  .copyright{position:absolute;left:0;width:703px;top:180px;text-align:center;font-size:6.3px;color:var(--faint)}
</style>
</head>
<body>
  <header class="hero">
    <div class="hero-photo" role="img" aria-label="Row of freight trucks parked at a depot at sunset with a glowing world network overlay"></div>
    <nav class="site-nav">
      <div class="brand">TQFREIGHT</div>
      <ul class="nav-links"><li>Home</li><li>Services</li><li>Industries</li><li>Contact</li></ul>
    </nav>
    <h1 class="hero-title">DRIVING<br><span class="accent">GLOBAL</span><br>COMMERCE</h1>
    <p class="hero-sub">Reliable and efficient freight solutions powering businesses worldwide.</p>
    <a class="btn">Get a Quote</a>
  </header>

  <section class="about">
    <div class="eyebrow">About Us</div>
    <h2 class="about-title">Professional<br>Typography</h2>
    <div class="about-copy">
      <p>We are primarily expertised the quality of logistics and supply chain to works. Our team standing extra to insure and express strain in the industries connection our businesses worldwide.</p>
      <p>We've arrived here to apply and promote on our amazing strong environment of a leading shipping and brand information company.</p>
    </div>
  </section>

  <h2 class="services-title">Our <span>Services</span></h2>

  <article class="card" style="left:72px;top:670px">
    <div class="card-icon"><svg width="16" height="16" viewBox="0 0 16 16" fill="none" stroke="#ee9460" stroke-width="1.1" stroke-linejoin="round"><path d="M2 12h12l-1.5 2h-9z"/><path d="M4 12V9h8v3"/><path d="M6 9V6h4v3"/><path d="M8 6V3"/></svg></div>
    <h3>Freight Forwarding</h3>
    <p>We expertise and direct freight forwarding in logistics and powerful main marketing in agency.</p>
  </article>
  <article class="card" style="left:358px;top:670px">
    <div class="card-icon"><svg width="16" height="16" viewBox="0 0 16 16" fill="none" stroke="#ee9460" stroke-width="1.1" stroke-linecap="round"><circle cx="8" cy="8" r="2.3"/><path d="M8 1.5v2M8 12.5v2M1.5 8h2M12.5 8h2M3.4 3.4l1.4 1.4M11.2 11.2l1.4 1.4M3.4 12.6l1.4-1.4M11.2 4.8l1.4-1.4"/></svg></div>
    <h3>Supply Chain Solutions</h3>
    <p>We are on automatic innovation and supply chain solutions, maintaining commerce in supply chain solutions.</p>
  </article>
  <article class="card" style="left:72px;top:815px">
    <div class="card-icon"><svg width="16" height="16" viewBox="0 0 16 16" fill="none" stroke="#ee9460" stroke-width="1.1" stroke-linejoin="round"><path d="M2.5 14V6.5L8 2.5l5.5 4V14z"/><path d="M5.5 14V9.5h5V14M2 14h12"/></svg></div>
    <h3>Warehousing</h3>
    <p>We are centered expert patch warehousing, employment, and connections valuable and military and insights.</p>
  </article>
  <article class="card" style="left:358px;top:815px">
    <div class="card-icon"><svg width="18" height="16" viewBox="0 0 18 16" fill="none" stroke="#ee9460" stroke-width="1.1" stroke-linejoin="round"><path d="M1.5 3.5h9v8h-9z"/><path d="M10.5 6.5h3l2.5 3v2h-5.5"/><circle cx="4.5" cy="12.5" r="1.5" fill="#34211b"/><circle cx="13" cy="12.5" r="1.5" fill="#34211b"/></svg></div>
    <h3>Specialized Transport</h3>
    <p>Heavy-duty transport systems freight heavy-duty volunteers, connection with specialized transport.</p>
  </article>

  <footer class="site-footer">
    <div class="foot-brand">TQFREIGHT</div>
    <p class="foot-about">Reliable and efficient freight solutions powering businesses worldwide.</p>
    <div class="foot-col contact" style="left:259px">
      <h4>Contact Info</h4>
      <ul>
        <li><svg width="6" height="7" viewBox="0 0 6 7"><path d="M3 7C1 4.5.5 3.5.5 2.5a2.5 2.5 0 015 0C5.5 3.5 5 4.5 3 7z" fill="#e05a4a"/></svg>Eastport, Dock 7</li>
        <li><svg width="7" height="7" viewBox="0 0 7 7"><path d="M1 .8l1.4-.3.8 1.7-.9.6c.4.9 1 1.5 1.9 1.9l.6-.9 1.7.8-.3 1.4C3.4 6 1 3.6 1 .8z" fill="#8c7f7a"/></svg>+100 555 0190</li>
        <li><svg width="7" height="6" viewBox="0 0 7 6"><rect x=".3" y=".8" width="6.4" height="4.4" fill="#8ea6c2"/><path d="M.3 .8L3.5 3.4 6.7.8" stroke="#fff" stroke-width=".6" fill="none"/></svg>info@tqfreightglobal.com</li>
        <li><svg width="7" height="7" viewBox="0 0 7 7"><circle cx="3.5" cy="3.5" r="3.1" fill="#5b8fc4"/></svg>www.tqfreightglobal.com</li>
      </ul>
    </div>
    <div class="foot-col" style="left:392px">
      <h4>Links</h4>
      <ul><li>Home</li><li>Services</li><li>Industries</li><li>Contact</li></ul>
    </div>
    <div class="foot-col" style="left:525px">
      <h4>Resources</h4>
      <ul><li>Terms and Use</li><li>Privacy</li><li>Site Map</li><li>Contact Us</li></ul>
    </div>
    <div class="foot-rule"></div>
    <p class="copyright">TQ Freight Global © 2022 Website Design</p>
  </footer>
</body>
</html>
```